Whitcombe Business Card Design

The name of the business is Dario Whitcombe, CPA LLC
The service that we offer is Accounting, Tax & Consulting Services. I need it to have the following items:
Dario Whitcombe, Principal
Phone Number
Email Address
Physical Address

I have attached the company logo, one in black and one in white. Please provide a design in black background and the other in white background. Please include "Accounting, Tax & Consulting Services". I want the business card to be clean and very professional.

```html
<!DOCTYPE html>
<html lang="en">
<head>
<meta charset="utf-8">
<title>Dario Whitcombe, CPA LLC – Business Card</title>
<link href="https://fonts.googleapis.com/css2?family=Montserrat:wght@500;600;700&family=Roboto:wght@300;400&display=swap" rel="stylesheet">
<style>
  :root {
    --page-bg: #2e2e2e;
    --card-dark: #222325;
    --card-dark-edge: #2c2d30;
    --ink-light: #f2f2f2;
    --ink-muted: #a9a9ab;
    --ink-silver: #c9c9cc;
    --brand-red: #8e1519;
    --brand-red-deep: #7a1014;
  }
  * { margin: 0; padding: 0; box-sizing: border-box; }
  html, body { width: 1200px; height: 1138px; overflow: hidden; background: var(--page-bg); }
  body { position: relative; font-family: "Roboto", sans-serif; }

  .card {
    position: absolute;
    border-radius: 16px;
    overflow: hidden;
    background: linear-gradient(135deg, var(--card-dark) 0%, var(--card-dark-edge) 100%);
    box-shadow: 0 6px 14px rgba(0,0,0,0.45);
  }

  /* Front */
  .card-front { left: 274px; top: 186px; width: 623px; height: 376px; }
  .front-name {
    position: absolute; left: 0; right: 0; top: 160px;
    text-align: center;
    font-family: "Montserrat", sans-serif; font-weight: 600;
    font-size: 30px; letter-spacing: 2px; color: var(--ink-silver);
  }
  .front-tagline {
    position: absolute; left: 0; right: 0; top: 329px;
    display: flex; justify-content: center; align-items: center; gap: 26px;
    font-weight: 300; font-size: 16.5px; color: var(--ink-light);
  }
  .front-tagline .rule { width: 38px; height: 2px; background: var(--brand-red); }

  /* Back */
  .card-back { left: 276px; top: 608px; width: 618px; height: 374px; }
  .accent-area {
    position: absolute; left: 0; right: 0; top: 170px; bottom: 0;
    background: linear-gradient(165deg, rgba(34,35,37,0) 0%, rgba(110,111,115,0.35) 38%, var(--brand-red) 62%, var(--brand-red-deep) 100%);
  }
  .brand-square {
    position: absolute; left: 34px; top: 60px; width: 66px; height: 66px;
    background: var(--brand-red);
  }
  .company-name {
    position: absolute; left: 130px; top: 67px;
    font-family: "Montserrat", sans-serif; font-weight: 600;
    font-size: 23px; color: var(--ink-light); letter-spacing: 0.5px;
  }
  .company-role {
    position: absolute; left: 131px; top: 97px;
    font-family: "Montserrat", sans-serif; font-weight: 600;
    font-size: 16px; letter-spacing: 2.6px; color: var(--ink-muted);
  }
  .person-name {
    position: absolute; left: 34px; top: 174px;
    font-family: "Montserrat", sans-serif; font-weight: 700;
    font-size: 21px; color: var(--ink-light);
  }
  .person-title {
    position: absolute; left: 34px; top: 202px;
    font-weight: 400; font-size: 17px; color: var(--ink-silver);
  }
  .contact {
    position: absolute; right: 31px; top: 246px;
    list-style: none; text-align: right;
    font-weight: 300; font-size: 16.5px; color: var(--ink-light);
  }
  .contact li { display: flex; justify-content: flex-end; align-items: center; gap: 12px; height: 24px; }
  .contact svg { width: 14px; height: 14px; fill: var(--ink-light); }
  .address {
    position: absolute; right: 31px; top: 322px;
    font-weight: 300; font-size: 17px; color: var(--ink-light);
  }
</style>
</head>
<body>

<section class="card card-front" aria-label="Card front">
  <div class="front-name">DARIO WHITCOMBE, CPA LLC</div>
  <div class="front-tagline">
    <span class="rule"></span>
    <span>Accounting, Tax &amp; Consulting Services</span>
    <span class="rule"></span>
  </div>
</section>

<section class="card card-back" aria-label="Card back">
  <div class="accent-area" role="img" aria-label="Decorative grey and red wave band across the lower card"></div>

  <div class="brand-square" aria-hidden="true"></div>
  <div class="company-name">DARIO WHITCOMBE, CPA LLC</div>
  <div class="company-role">CERTIFIED PUBLIC ACCOUNTANT</div>

  <div class="person-name">DARIO WHITCOMBE</div>
  <div class="person-title">Principal</div>

  <ul class="contact">
    <li>828-555-0147
      <svg viewBox="0 0 16 16" aria-hidden="true"><path d="M2 5c0-2 3-3 6-3s6 1 6 3v1h-3V5H5v1H2zM4 7h8l2 6H2zm4 1.5a2 2 0 100 4 2 2 0 000-4z"/></svg>
    </li>
    <li>dw@dariowhitcombellc.com
      <svg viewBox="0 0 16 16" aria-hidden="true"><path d="M1 3h14v10H1zm1.5 1.2v.3L8 9l5.5-4.5v-.3zM2.5 6v5.8h11V6L8 10.5z"/></svg>
    </li>
    <li>www.dariowhitcombellc.com
      <svg viewBox="0 0 16 16" aria-hidden="true"><path d="M8 1a7 7 0 100 14A7 7 0 008 1zm0 1.3c.8 0 1.7 1.5 2 3.7H6c.3-2.2 1.2-3.7 2-3.7zM2.4 7h2.6v2H2.4a5.8 5.8 0 010-2zm3.6 0h4v2H6zm5 0h2.6a5.8 5.8 0 010 2H11zM6 10h4c-.3 2.2-1.2 3.7-2 3.7S6.3 12.2 6 10z"/></svg>
    </li>
  </ul>
  <div class="address">418, Larkspur Ave, Fairmont, US 2871</div>
</section>

</body>
</html>
```